Upmarket Dessert Lounge needs a Business Card Design

We are an upmarket dessert lounge needing a business card to match our image.

We want something that is simple yet beautiful, feminine, classy, sophisticated and elegant. We want it to stand out and don't mind if it is bold.

The design should include our logo and colours of red or maroon with gold highlights. We don't mind if black is used.

Marlow & Quince

Target Market(s)

For those who like to indulge or treat themselves and give in to their temptations on good quality desserts.

Industry/Entity Type

Business

Requirements
Must have
• Must include our logo and our name

Marlow & Quince

M & Q

```html
<!DOCTYPE html>
<html lang="en">
<head>
<meta charset="utf-8">
<title>Marlow &amp; Quince — Business Card</title>
<link rel="stylesheet" href="https://fonts.googleapis.com/css2?family=Open+Sans:wght@400;700&display=swap">
<style>
  :root {
    --backdrop: #c9c9cb;
    --card-black: #000000;
    --maroon: #7b1416;
    --cream: #fdd49b;
    --ink-white: #ffffff;
    --text-font: "Open Sans", Arial, sans-serif;
  }
  html, body {
    margin: 0;
    padding: 0;
    overflow: hidden;
  }
  .canvas {
    position: relative;
    width: 956px;
    height: 1200px;
    background: var(--backdrop);
    overflow: hidden;
    font-family: var(--text-font);
  }
  .card {
    position: absolute;
    width: 798px;
    height: 454px;
    background: var(--card-black);
    border-radius: 26px;
    overflow: hidden;
  }
  .card--front { left: 69px; top: 97px; }
  .card--back  { left: 74px; top: 633px; }

  .card__swoosh {
    position: absolute;
    left: 0;
    top: 0;
    width: 798px;
    height: 454px;
  }

  .brand-name {
    position: absolute;
    left: 0;
    right: 0;
    text-align: center;
    color: var(--cream);
    font-family: var(--text-font);
    font-weight: 400;
    margin: 0;
    white-space: nowrap;
  }
  .card--front .brand-name {
    top: 90px;
    font-size: 34px;
    letter-spacing: 1px;
  }
  .card--back .brand-name {
    top: 160px;
    font-size: 96px;
    line-height: 1;
  }

  .holder {
    position: absolute;
    left: 0;
    right: 0;
    top: 232px;
    text-align: center;
    color: var(--ink-white);
    font-size: 22px;
    margin: 0;
  }
  .holder__name { font-weight: 700; }
  .holder__role { font-weight: 400; letter-spacing: 0.5px; }

  .contacts {
    position: absolute;
    left: 0;
    right: 0;
    top: 288px;
    text-align: center;
    color: var(--ink-white);
    font-size: 17px;
    line-height: 28px;
    margin: 0;
  }
  .contacts b { font-weight: 700; }
  .contacts .sep { margin: 0 6px; }

  .address {
    position: absolute;
    left: 400px;
    width: 290px;
    top: 387px;
    text-align: center;
    color: var(--ink-white);
    font-size: 17px;
    line-height: 27px;
    margin: 0;
  }
</style>
</head>
<body>
<main class="canvas">

  <section class="card card--front" aria-label="Business card front">
    <svg class="card__swoosh" viewBox="0 0 798 454" aria-hidden="true">
      <path d="M0,454 L0,447 Q260,352 420,356 Q650,362 798,382 L798,454 Z" fill="var(--maroon)"/>
      <path d="M0,446 Q200,378 420,356 Q200,366 0,400 Z" fill="var(--card-black)"/>
      <path d="M0,436 Q200,372 410,356 Q200,368 0,404 Z" fill="var(--cream)"/>
    </svg>

    <h1 class="brand-name">MARLOW &amp; QUINCE</h1>

    <p class="holder">
      <span class="holder__name">Your Name -</span>
      <span class="holder__role">Designation</span>
    </p>

    <p class="contacts">
      <b>p</b> : 123-456-7890<span class="sep">|</span><b>c</b> : 123-456-7890<span class="sep">|</span><b>f</b> : 123-456-7890<br>
      <b>e</b> : name@yourwebsite.com<span class="sep">|</span><b>w</b> : www.marlow&amp;quince.com
    </p>

    <p class="address">0000, Street Name<br>City Name, Country Code.</p>
  </section>

  <section class="card card--back" aria-label="Business card back">
    <p class="brand-name">M &amp; Q</p>
  </section>

</main>
</body>
</html>
```